Business card for law firm

Need business card for new law firm. Think confident, authoritative, conservative, but not stuffy or old-fashioned.

Contact Information for Business Card

Content for card - logo (uploaded), plus the following:

Paul Whitcombe (larger font)
Managing Partner (larger font, but not as large as name)
Level 9, 7 Ferris Lane
Sydney NSW 2000
Main Tel 02 9364 2710
Direct Tel 02 8472 3159
Email paul@qvlegal.com.au
www.qvlegal.com.au

Letterhead design should include logo plus:
Level 9, 7 Ferris Lane
Sydney NSW 2000
Tel 02 8472 3159
www.qvlegal.com.au

```html
<!DOCTYPE html>
<html lang="en">
<head>
<meta charset="utf-8">
<title>Quayvale Legal — Business Card</title>
<link rel="stylesheet" href="https://fonts.googleapis.com/css2?family=Arimo:wght@400;700&display=swap">
<style>
  :root {
    --backdrop: #aab1b2;
    --paper: #f4f3ef;
    --navy: #141f3d;
    --ink: #3a3a3a;
    --ink-strong: #1c1c1c;
  }
  * { margin: 0; padding: 0; box-sizing: border-box; }
  html, body { width: 1200px; height: 824px; overflow: hidden; }
  body {
    background: var(--backdrop);
    position: relative;
    font-family: "Arimo", Arial, sans-serif;
  }
  .card {
    position: absolute;
    width: 500px;
    height: 304px;
    background: var(--paper);
    box-shadow: 0 2px 6px rgba(0,0,0,0.12);
  }
  .card--contact { left: 70px; top: 260px; }
  .card--brand { left: 630px; top: 260px; }

  /* contact side */
  .contact { position: absolute; left: 38px; top: 34px; }
  .contact__name {
    font-size: 28px; font-weight: 700; color: var(--navy); line-height: 1.05;
  }
  .contact__role {
    font-size: 19px; color: var(--ink-strong); margin-bottom: 12px;
  }
  .contact__line {
    font-size: 13.5px; color: var(--ink); line-height: 1.45;
  }
  .contact__line--gap { margin-top: 8px; }
  .contact__web {
    font-size: 14px; font-weight: 700; color: var(--ink-strong); margin-top: 8px;
  }
  .contact__mark {
    position: absolute; right: 36px; bottom: 34px;
    display: flex; align-items: center; gap: 10px;
    font-family: "Arimo", Arial, sans-serif; font-size: 18px; font-weight: 400;
    color: var(--navy);
  }
  .mark-square { width: 22px; height: 22px; background: var(--navy); flex: none; }

  /* brand side */
  .brand {
    position: absolute; inset: 0;
    display: flex; flex-direction: column; align-items: center; justify-content: center;
  }
  .brand__square { width: 44px; height: 44px; background: var(--navy); margin-bottom: 18px; }
  .brand__name {
    font-family: "Arimo", Arial, sans-serif; font-size: 34px; font-weight: 400;
    color: var(--ink-strong); line-height: 1.1;
  }
</style>
</head>
<body>
  <section class="card card--contact" aria-label="Contact side">
    <div class="contact">
      <p class="contact__name">Paul Whitcombe</p>
      <p class="contact__role">Managing Partner</p>
      <p class="contact__line">Level 9, 7 Ferris Lane</p>
      <p class="contact__line">Sydney NSW 2000</p>
      <p class="contact__line contact__line--gap">02 9364 2710 (Main)</p>
      <p class="contact__line">02 8472 3159 (Direct)</p>
      <p class="contact__line">paul@qvlegal.com.au</p>
      <p class="contact__web">qvlegal.com.au</p>
    </div>
    <div class="contact__mark"><span class="mark-square"></span>Quayvale Legal</div>
  </section>

  <section class="card card--brand" aria-label="Brand side">
    <div class="brand">
      <span class="brand__square"></span>
      <p class="brand__name">Quayvale Legal</p>
    </div>
  </section>
</body>
</html>
```